Business Card Design for Training Business

Clear Path Coaching is a new business that delivers training and other services with a focus on topics related to mental health and wellbeing, for example, Wellmind Response Course, Resilience etc. We have a strong focus on evidence-based psychology and neuroscience. I have a logo which I will upload with the brief, so please consider colours that work well with the logo.
Target Market(s)
Adults, workplaces (particularly government and not-for-profits)
Industry/Entity Type
Business
Contact Information for Business Card
Head Strong TrainingSamantha SellwoodDirector0438 770 850sam@headstrongtraining.com.auwww.headstrongtraining.com.au

```html
<!DOCTYPE html>
<html lang="en">
<head>
<meta charset="utf-8">
<title>Clear Path Coaching – Business Card</title>
<link href="https://fonts.googleapis.com/css2?family=Questrial&display=swap" rel="stylesheet">
<style>
  :root {
    --teal: #25b5b9;
    --teal-soft: #7fc9b4;
    --ring: #4a3c37;
    --paper: #f6f6f4;
    --ink-light: #ffffff;
    --ink-grey: #7a7574;
    --backdrop: #e9e9e9;
  }
  * { margin: 0; padding: 0; box-sizing: border-box; }
  html, body {
    width: 1200px;
    height: 750px;
    overflow: hidden;
    background: var(--backdrop);
    font-family: "Questrial", "Century Gothic", sans-serif;
  }
  .sheet {
    width: 1200px;
    height: 750px;
    display: flex;
    flex-direction: column;
    align-items: center;
    justify-content: center;
    gap: 22px;
  }
  .card {
    position: relative;
    width: 480px;
    height: 275px;
    border-radius: 14px;
    overflow: hidden;
  }
  .card__pattern {
    position: absolute;
    inset: 0;
  }
  .card--front .card__pattern {
    background: radial-gradient(circle at 50% 50%, var(--teal-soft) 0%, #bfe3dc 45%, var(--paper) 100%);
  }
  .card--back .card__pattern {
    background: var(--teal);
  }
  .card__disc {
    position: absolute;
    left: 50%;
    top: 50%;
    width: 242px;
    height: 242px;
    transform: translate(-50%, -50%);
    border-radius: 50%;
    border: 3px solid var(--ring);
    display: flex;
    flex-direction: column;
    align-items: center;
    justify-content: center;
    text-align: center;
  }
  .card--front .card__disc {
    background: var(--teal);
    box-shadow: 0 0 0 3px var(--teal);
    color: var(--ink-light);
  }
  .card--back .card__disc {
    background: var(--paper);
    box-shadow: 0 0 0 3px var(--paper);
    color: var(--ink-grey);
  }
  .contact__name { font-size: 18px; letter-spacing: 0.3px; line-height: 1.1; }
  .contact__role { font-size: 13px; margin-top: 2px; }
  .contact__details {
    list-style: none;
    margin-top: 14px;
    font-size: 12.5px;
    line-height: 1.45;
  }
  .brand__dot {
    width: 62px;
    height: 62px;
    border-radius: 50%;
    border: 2px solid var(--teal);
    margin-bottom: 18px;
  }
  .brand__name {
    font-size: 19px;
    letter-spacing: 2px;
    line-height: 1.2;
  }
  .brand__name span {
    display: block;
    font-size: 10px;
    letter-spacing: 4px;
    margin-top: 3px;
  }
</style>
</head>
<body>
  <main class="sheet">
    <section class="card card--front">
      <div class="card__pattern" role="img" aria-label="Radiating teal and green line rosette pattern on white"></div>
      <div class="card__disc">
        <p class="contact__name">Rebecca Tanfield</p>
        <p class="contact__role">Director</p>
        <ul class="contact__details">
          <li>0491 362 517</li>
          <li>bec@clearpathcoaching.example.au</li>
          <li>www.clearpathcoaching.example.au</li>
        </ul>
      </div>
    </section>

    <section class="card card--back">
      <div class="card__pattern" role="img" aria-label="Radiating white line rosette pattern on teal"></div>
      <div class="card__disc">
        <div class="brand__dot"></div>
        <p class="brand__name">CLEAR PATH<span>COACHING</span></p>
      </div>
    </section>
  </main>
</body>
</html>
```